Business Card for Vorla Parts Wholesale supplier

Hi There! I need a new business card for our company. We are specialized in selling Vorla parts, mostly we sell new LCD screens for Zelnar and Drelks. I would like to see that back in the design.

You can find the colors and logo's on our website: www.hartuvo.nl

Industry/Entity Type

Business

Contact Information for Business Card

My Details:
Tobias Lindqvist

Phone: 0031687203316
E-mail: Tobias@hartuvo.nl

Slogan: "Because Quality Matters"

Font styles to use
Sans Serif

Colors

Designer to choose colors to be used in the design.

Requirements
Must have
• A Black backside with the Hartuvo logo on it. The front side should be clean with only my contact details.
• But I'm also open for something really different or awesome!
Nice to have
• Remember that we are in the parts & repairing industry, So i'll be handing those business cards mainly to repair companies. Maybe you can do something with that thought :)

```html
<!DOCTYPE html>
<html lang="en">
<head>
<meta charset="utf-8">
<title>Hartuvo business card</title>
<link href="https://fonts.googleapis.com/css2?family=Open+Sans:wght@400;600;800&display=swap" rel="stylesheet">
<style>
  :root {
    --stage: #2b2b2d;
    --card-black: #050505;
    --card-white: #ffffff;
    --orange: #f47321;
    --ink: #111111;
    --rule: #3a3a3a;
  }
  * { box-sizing: border-box; margin: 0; padding: 0; }
  html, body { width: 1200px; height: 880px; overflow: hidden; }
  body {
    background: var(--stage);
    font-family: "Open Sans", Arial, sans-serif;
    position: relative;
  }
  .card {
    position: absolute;
    width: 540px;
    height: 310px;
    border-radius: 22px;
    box-shadow: 0 18px 40px rgba(0,0,0,.45);
    overflow: hidden;
  }
  .card-back { left: 40px; top: 170px; background: var(--card-black); }
  .card-front { left: 620px; top: 400px; background: var(--card-white); }

  .brand {
    position: absolute;
    display: flex;
    align-items: center;
    gap: 14px;
  }
  .brand-square {
    width: 46px; height: 46px;
    background: var(--orange);
    border-radius: 6px;
  }
  .brand-name {
    font-weight: 800;
    font-size: 58px;
    letter-spacing: 1px;
    line-height: 1;
  }
  .card-back .brand { left: 112px; top: 112px; }
  .card-back .brand-name { color: #ffffff; }
  .card-back .tagline {
    position: absolute; left: 0; right: 0; top: 200px;
    text-align: center; color: #ffffff;
    font-size: 14px; font-weight: 600;
  }

  .card-front .brand { left: 34px; top: 96px; }
  .card-front .brand-name { color: var(--ink); font-size: 54px; }
  .holder-name {
    position: absolute; right: 34px; top: 68px;
    color: var(--orange); font-weight: 600; font-size: 19px;
  }
  .name-rule {
    position: absolute; right: 30px; top: 98px;
    width: 250px; height: 1px; background: var(--rule);
  }
  .card-front .tagline {
    position: absolute; right: 34px; top: 176px;
    color: var(--ink); font-size: 14px; font-weight: 600;
  }
  .contact-rule {
    position: absolute; left: 34px; top: 212px;
    width: 230px; height: 1px; background: var(--rule);
  }
  .contact-list {
    position: absolute; left: 34px; top: 222px;
    list-style: none;
  }
  .contact-list li {
    display: flex; align-items: center; gap: 10px;
    font-size: 15px; color: var(--ink); height: 24px;
  }
  .contact-icon {
    width: 18px; height: 18px; border-radius: 4px;
    background: var(--orange);
    display: flex; align-items: center; justify-content: center;
  }
  .accent { color: var(--orange); }
</style>
</head>
<body>
  <section class="card card-back" aria-label="Card back">
    <div class="brand">
      <span class="brand-square"></span>
      <span class="brand-name">hartuvo</span>
    </div>
    <p class="tagline">Because Quality Matters</p>
  </section>

  <section class="card card-front" aria-label="Card front">
    <div class="brand">
      <span class="brand-square"></span>
      <span class="brand-name">hartuvo</span>
    </div>
    <p class="holder-name">Tobias Lindqvist</p>
    <span class="name-rule"></span>
    <p class="tagline">Because Quality Matters</p>
    <span class="contact-rule"></span>
    <ul class="contact-list">
      <li>
        <span class="contact-icon">
          <svg width="12" height="12" viewBox="0 0 12 12"><path d="M2.5 1h2l1 2.5-1.3 1a6 6 0 0 0 3.3 3.3l1-1.3L11 7.5v2A1.5 1.5 0 0 1 9.5 11 8.5 8.5 0 0 1 1 2.5 1.5 1.5 0 0 1 2.5 1z" fill="#fff"/></svg>
        </span>
        0031687203316
      </li>
      <li>
        <span class="contact-icon">
          <svg width="12" height="12" viewBox="0 0 12 12"><rect x="1" y="2.5" width="10" height="7" rx="1" fill="#fff"/><path d="M1.5 3l4.5 3.5L10.5 3" stroke="#f47321" stroke-width="1" fill="none"/></svg>
        </span>
        Tobias@hartuvo.nl
      </li>
      <li>
        <span class="contact-icon">
          <svg width="12" height="12" viewBox="0 0 12 12" fill="none" stroke="#fff" stroke-width="1"><circle cx="6" cy="6" r="4.5"/><ellipse cx="6" cy="6" rx="2" ry="4.5"/><path d="M1.5 6h9"/></svg>
        </span>
        <span>www.<span class="accent">hartuvo</span>.nl</span>
      </li>
    </ul>
  </section>
</body>
</html>
```